Website for Apartment Rental in Prague

I would like to create designs of my website focused on luxury apartment rentals in Prague, Czech Republic. I created initial mock-ups, They are all attached. I need to design homepage and subpage. The mock-ups were created by combining elements from different websites that I liked but I need you to create a design that is unique and original. The attached files a only a guidance for the structure of the website but not for the design. Try to be creative.

Apartment

```html
<!DOCTYPE html>
<html lang="en">
<head>
<meta charset="utf-8">
<title>Maison Lyra Apartment Prague</title>
<link rel="stylesheet" href="https://fonts.googleapis.com/css2?family=Montserrat:wght@400;500;600;700&family=EB+Garamond:wght@600&family=Jost:ital@1&display=swap">
<style>
:root{
  --accent:#f7ae00;
  --ink:#1b1b1b;
  --text:#333;
  --muted:#666;
  --line:#d9d9d9;
  --panel:#eeeeee;
  --white:#fff;
  --footer:#141414;
  --topbar:rgba(20,20,20,.72);
}
*{box-sizing:border-box;margin:0;padding:0}
html,body{width:1200px;height:2293px;overflow:hidden}
body{position:relative;font-family:"Montserrat",Arial,sans-serif;color:var(--text);background:var(--white)}
.hero{position:absolute;left:0;top:0;width:1200px;height:628px;background:linear-gradient(160deg,#8fb4d6 0%,#c9a77a 35%,#a57a4a 60%,#6b4a2c 100%)}
.hero-title{position:absolute;left:0;right:0;top:336px;text-align:center;font-family:"EB Garamond",Georgia,serif;font-weight:600;font-size:42px;letter-spacing:3px;color:var(--white);text-shadow:0 2px 6px rgba(0,0,0,.45)}
.hero-dots{position:absolute;top:602px;left:0;right:0;display:flex;justify-content:center;gap:4px}
.hero-dots span{width:8px;height:8px;border-radius:50%;border:1px solid var(--white)}
.hero-dots span.on{background:var(--white)}
.masthead{position:absolute;left:0;top:0;width:1200px;height:115px;background:var(--topbar);color:var(--white)}
.util{position:absolute;top:34px;left:142px;right:142px;display:flex;align-items:center;font-size:12px;font-weight:500}
.lang{border:1px solid var(--white);padding:1px 5px;font-size:11px;margin-right:34px}
.util a{display:flex;align-items:center;gap:8px;margin-right:30px;color:var(--white);text-decoration:none}
.brand{position:absolute;left:0;right:0;top:18px;text-align:center;font-size:16px;font-weight:600;line-height:22px;color:var(--white)}
.contact{position:absolute;right:142px;top:34px;display:flex;gap:22px;font-size:12px}
.contact span{display:flex;align-items:center;gap:8px}
.contact .phone{font-weight:700;font-size:13px}
.nav{position:absolute;top:88px;left:142px;right:142px;display:flex;justify-content:space-between;font-size:12px;font-weight:600}
.booking{position:absolute;top:686px;left:142px;width:916px}
.booking h2{text-align:center;font-size:25px;font-weight:600;color:var(--ink)}
.hl{color:var(--accent)}
.form{display:flex;margin-top:30px;gap:11px;align-items:flex-end}
.field label{display:block;font-size:11px;font-weight:500;color:var(--ink);margin-bottom:8px}
.box{height:34px;border:1px solid var(--line);border-radius:3px;display:flex;align-items:center;justify-content:space-between;padding:0 9px;font-size:11px;color:var(--text)}
.btn-check{height:34px;width:127px;background:var(--accent);color:var(--white);border-radius:3px;display:flex;align-items:center;justify-content:center;font-size:11px;font-weight:600}
.vision{position:absolute;top:862px;left:0;width:1200px;height:503px;background:var(--panel);text-align:center}
.vision h2{margin-top:56px;font-size:23px;font-weight:600;color:var(--ink)}
.vision p.lead{width:860px;margin:22px auto 0;font-size:12.5px;line-height:20px;color:var(--text)}
.badge{width:54px;height:54px;border:2px solid var(--accent);border-radius:50%;margin:20px auto 0;display:flex;align-items:center;justify-content:center}
.designed{margin-top:12px;font-size:13px;font-weight:600;color:var(--ink);line-height:18px}
.quote{position:relative;width:788px;margin:20px auto 0;padding:22px 70px;background:var(--white);border-radius:8px;transform:skewX(-3deg);box-shadow:0 2px 8px rgba(0,0,0,.05)}
.quote::before{content:"";position:absolute;top:-14px;left:376px;border:14px solid transparent;border-top:0;border-bottom-color:var(--white)}
.quote p{transform:skewX(3deg);font-family:"Jost",Arial,sans-serif;font-style:italic;font-size:12.5px;line-height:21px;color:var(--text)}
.grid{position:absolute;top:1431px;left:142px;width:916px;display:grid;grid-template-columns:repeat(3,289px);column-gap:25px;row-gap:29px}
.card{position:relative;height:362px;border:1px solid var(--line);border-radius:3px;background:var(--white)}
.card .photo{position:absolute;left:8px;top:8px;width:271px;height:171px}
.ribbon{position:absolute;left:-6px;top:18px;background:var(--accent);color:var(--white);font-size:10.5px;font-weight:600;padding:4px 10px}
.card h3{position:absolute;left:16px;right:14px;top:190px;font-size:12.5px;font-weight:600;line-height:17px;color:var(--ink)}
.card .desc{position:absolute;left:16px;right:14px;top:226px;font-size:12px;line-height:17px;color:var(--text)}
.meta{position:absolute;left:16px;top:295px;display:flex;gap:22px;font-size:12px}
.meta span{display:flex;align-items:center;gap:7px}
.card .foot{position:absolute;left:0;right:0;bottom:0;height:40px;border-top:1px solid var(--line);display:flex;align-items:center;justify-content:space-between;padding:0 16px 0 18px;font-size:12px;font-weight:600;color:var(--ink)}
.btn-book{border:2px solid var(--accent);padding:4px 12px;font-size:12px;font-weight:600}
.know{height:362px;border:1px solid var(--line);border-radius:3px;text-align:center;background:var(--white)}
.know h3{background:var(--accent);color:var(--white);font-size:21px;font-weight:500;height:54px;line-height:54px}
.know .item{margin:0 16px;padding:21px 0 18px;border-bottom:1px solid var(--line)}
.know .item:last-child{border-bottom:0}
.know h4{font-size:14px;font-weight:700;color:var(--ink)}
.know p{font-size:12px;line-height:17px;margin-top:7px;color:var(--text)}
.footer{position:absolute;left:0;top:2248px;width:1200px;height:45px;background:var(--footer);color:var(--white);font-size:11px}
.footer .copy{position:absolute;left:142px;top:16px}
.social{position:absolute;left:698px;top:11px;display:flex;gap:7px}
.social span{width:24px;height:24px;border-radius:50%}
.msg{position:absolute;left:838px;top:2238px;width:220px;height:46px;background:var(--accent);color:var(--white);display:flex;align-items:center;justify-content:center;gap:9px;font-size:15px;font-weight:500}
</style>
</head>
<body>

<section class="hero" role="img" aria-label="Sunlit apartment bedroom with wooden floor and large windows over Prague rooftops">
  <h1 class="hero-title">Being Home In Prague</h1>
  <div class="hero-dots"><span class="on"></span><span></span><span></span><span></span></div>
</section>

<header class="masthead">
  <div class="util">
    <span class="lang">EN ▾</span>
    <a>Our Hospitality</a>
    <a><svg width="13" height="13" viewBox="0 0 13 13"><path d="M2 1v12M2 2h9l-2 3 2 3H2" fill="#fff" stroke="#fff"/></svg>Discover Prague</a>
  </div>
  <div class="brand">Maison Lyra<br>Apartment Prague</div>
  <div class="contact">
    <span><svg width="14" height="12" viewBox="0 0 14 12"><rect x="1" y="1" width="12" height="10" fill="none" stroke="#fff"/><path d="M1 1l6 5 6-5" fill="none" stroke="#fff"/></svg>bookings@lyrastays.example</span>
    <span class="phone"><svg width="13" height="13" viewBox="0 0 24 24"><path fill="#fff" d="M6.6 10.8a15 15 0 006.6 6.6l2.2-2.2a1 1 0 011-.25 11.4 11.4 0 003.6.6 1 1 0 011 1V20a1 1 0 01-1 1A17 17 0 013 4a1 1 0 011-1h3.5a1 1 0 011 1c0 1.25.2 2.45.57 3.57a1 1 0 01-.25 1z"/></svg>420 555 014 268</span>
  </div>
  <nav class="nav">
    <span>Apartments</span><span>Location</span><span>Services</span><span>Gallery</span><span>News</span><span>Exclusive Offers &amp; Tours</span><span>For Families</span><span>Contact Us</span>
  </nav>
</header>

<section class="booking">
  <h2>Official Site - <span class="hl">Best Price Guaranteed</span></h2>
  <div class="form">
    <div class="field" style="width:149px"><label>Check In Date</label><div class="box">11/19/2017 <svg width="13" height="13" viewBox="0 0 13 13"><rect x="1" y="2" width="11" height="10" fill="none" stroke="#555"/><path d="M1 5h11M4 0v3M9 0v3" stroke="#555"/></svg></div></div>
    <div class="field" style="width:150px"><label>Check Out Date</label><div class="box">11/21/2017 <svg width="13" height="13" viewBox="0 0 13 13"><rect x="1" y="2" width="11" height="10" fill="none" stroke="#555"/><path d="M1 5h11M4 0v3M9 0v3" stroke="#555"/></svg></div></div>
    <div class="field" style="width:53px"><label>Adults</label><div class="box">02 <svg width="10" height="6"><path d="M1 1l4 4 4-4" fill="none" stroke="#555"/></svg></div></div>
    <div class="field" style="width:58px"><label>Childrens</label><div class="box">01 <svg width="10" height="6"><path d="M1 1l4 4 4-4" fill="none" stroke="#555"/></svg></div></div>
    <div class="field" style="width:58px"><label>Infants</label><div class="box">00 <svg width="10" height="6"><path d="M1 1l4 4 4-4" fill="none" stroke="#555"/></svg></div></div>
    <div class="field" style="width:120px"><label>Promotional Code</label><div class="box"></div></div>
    <div class="btn-check">Check Availability</div>
    <div class="field" style="width:121px"><label>OR</label><div class="box" style="font-size:10px">Select Rental Unit <svg width="10" height="6"><path d="M1 1l4 4 4-4" fill="none" stroke="#555"/></svg></div></div>
  </div>
</section>

<section class="vision">
  <h2>A Different <span class="hl">Vision Of Travelling</span></h2>
  <p class="lead">Something spectacular has arrived in the heart of Europe. Steps from Old Town, this rental experience is curated with world-class amenities, exemplary style and a level of convenience you have to experience to believe. Experience the different vision of luxury in center of Prague.</p>
  <div class="badge"><svg width="24" height="24" viewBox="0 0 24 24" fill="none" stroke="#f7ae00" stroke-width="1.6"><path d="M4 4h16v6H4zM6 10v4h12v-4M7 14l-3 8M17 14l3 8M7 14l10 8M17 14L7 22"/></svg></div>
  <div class="designed">Interiors Designed<br>By: <span class="hl">Maison Lyra</span></div>
  <div class="quote"><p>At Maison Lyra we offer short term as well as long term options in our studio apartments and our one bedroom apartment homes. Our luxurious apartments and high quality customer service have allowed us to dominate the Prague apartment market with a proven track record. Our years of experience and knowledge have made us a premier apartment rental company as we continue to stress the importance of servicing individuals and corporations who are seeking the finest accommodations.</p></div>
</section>

<section class="grid">
  <article class="card">
    <div class="photo" role="img" aria-label="Bright open kitchen and dining room with white table" style="background:linear-gradient(135deg,#e8e2d8,#b89b7a 60%,#6b5a48)"></div>
    <span class="ribbon">From 150 USD</span>
    <h3>Brand New Luxury Living Shinning Contemporary Design</h3>
    <p class="desc" style="top:226px">The 22nd issue is dedicated to colors...</p>
    <div class="meta"><span><svg width="18" height="12" viewBox="0 0 18 12"><path fill="#f7ae00" d="M0 1h2v5h16v6h-2v-2H2v2H0zM3 3h4v3H3zM8 3h8a2 2 0 012 2v1H8z"/></svg>1 Bedroom</span><span><svg width="12" height="13" viewBox="0 0 12 13"><circle cx="6" cy="3.5" r="3" fill="#f7ae00"/><path d="M0 13a6 6 0 0112 0z" fill="#f7ae00"/></svg>Max 4 People</span></div>
    <div class="foot"><span>Details</span><span class="btn-book">Book Now</span></div>
  </article>
  <article class="card">
    <div class="photo" role="img" aria-label="Grey living room with dining set and sofa" style="background:linear-gradient(135deg,#9aa0a6,#d8d6d2 55%,#7d7a78)"></div>
    <span class="ribbon">From 150 USD</span>
    <h3>Brand New Zen Luxury Living Apartment In The Center Of Prague</h3>
    <p class="desc">Recognized with Wanderline Journal 2017 Readers' Choice Award #1 hotel in the world...</p>
    <div class="meta"><span><svg width="18" height="12" viewBox="0 0 18 12"><path fill="#f7ae00" d="M0 1h2v5h16v6h-2v-2H2v2H0zM3 3h4v3H3zM8 3h8a2 2 0 012 2v1H8z"/></svg>1 Bedroom</span><span><svg width="12" height="13" viewBox="0 0 12 13"><circle cx="6" cy="3.5" r="3" fill="#f7ae00"/><path d="M0 13a6 6 0 0112 0z" fill="#f7ae00"/></svg>Max 4 People</span></div>
    <div class="foot"><span>Details</span><span class="btn-book">Book Now</span></div>
  </article>
  <article class="card">
    <div class="photo" role="img" aria-label="Wooden kitchen with dining table and window" style="background:linear-gradient(135deg,#c89a5c,#e6dccb 55%,#8a6a44)"></div>
    <span class="ribbon">From 150 USD</span>
    <h3>Expedition Prague! Top Location Brand New Apartment</h3>
    <p class="desc">for your management committee, showroom session, incentive trip, product launch, privatization...</p>
    <div class="meta"><span><svg width="18" height="12" viewBox="0 0 18 12"><path fill="#f7ae00" d="M0 1h2v5h16v6h-2v-2H2v2H0zM3 3h4v3H3zM8 3h8a2 2 0 012 2v1H8z"/></svg>1 Bedroom</span><span><svg width="12" height="13" viewBox="0 0 12 13"><circle cx="6" cy="3.5" r="3" fill="#f7ae00"/><path d="M0 13a6 6 0 0112 0z" fill="#f7ae00"/></svg>Max 4 People</span></div>
    <div class="foot"><span>Details</span><span class="btn-book">Book Now</span></div>
  </article>
  <article class="card">
    <div class="photo" role="img" aria-label="Warm living room with red sofa and wooden floor" style="background:linear-gradient(135deg,#e9dcc2,#cfa871 55%,#c65a4a)"></div>
    <span class="ribbon">From 150 USD</span>
    <h3>Brand New Zen Luxury Living Apartment In The Center Of Prague</h3>
    <p class="desc">The 22nd issue is dedicated to colors...</p>
    <div class="meta"><span><svg width="18" height="12" viewBox="0 0 18 12"><path fill="#f7ae00" d="M0 1h2v5h16v6h-2v-2H2v2H0zM3 3h4v3H3zM8 3h8a2 2 0 012 2v1H8z"/></svg>1 Bedroom</span><span><svg width="12" height="13" viewBox="0 0 12 13"><circle cx="6" cy="3.5" r="3" fill="#f7ae00"/><path d="M0 13a6 6 0 0112 0z" fill="#f7ae00"/></svg>Max 4 People</span></div>
    <div class="foot"><span>Details</span><span class="btn-book">Book Now</span></div>
  </article>
  <article class="card">
    <div class="photo" role="img" aria-label="Modern white bedroom with blue rug and tall windows" style="background:linear-gradient(135deg,#f1ece6,#d9c9b6 55%,#6f8fa6)"></div>
    <span class="ribbon">From 150 USD</span>
    <h3>Brand New Modern Apartment Unbeatable Location</h3>
    <p class="desc">Recognized with Wanderline Journal 2017</p>
    <div class="meta"><span><svg width="18" height="12" viewBox="0 0 18 12"><path fill="#f7ae00" d="M0 1h2v5h16v6h-2v-2H2v2H0zM3 3h4v3H3zM8 3h8a2 2 0 012 2v1H8z"/></svg>1 Bedroom</span><span><svg width="12" height="13" viewBox="0 0 12 13"><circle cx="6" cy="3.5" r="3" fill="#f7ae00"/><path d="M0 13a6 6 0 0112 0z" fill="#f7ae00"/></svg>Max 4 People</span></div>
    <div class="foot"><span>Details</span><span class="btn-book">Book Now</span></div>
  </article>
  <aside class="know">
    <h3>Need To Know</h3>
    <div class="item"><h4>APARTMENTS</h4><p>Also Avaliable To Rent All The Apartments Together For Companies Or Larger Groups,</p></div>
    <div class="item"><h4>CHECK-OUT</h4><p>12 Noon; Earliest Check-in, 3PM- Both Are Flexible, By Arragement.</p></div>
    <div class="item"><h4>RATES</h4><p>Prices From 150 USD Per Night Including Tax</p></div>
  </aside>
</section>

<footer class="footer">
  <span class="copy">Copyright © 2017 Maison Lyra Apartment Prague. All Rights Reserved.</span>
  <div class="social"><span style="background:#3b5998"></span><span style="background:#1da1f2"></span><span style="background:#0077b5"></span><span style="background:#dd4b39"></span></div>
</footer>
<div class="msg"><svg width="20" height="18" viewBox="0 0 20 18"><path d="M10 1C4.5 1 1 4.3 1 8c0 2 1 3.7 2.7 4.9L3 17l4.3-2.4c.9.2 1.8.4 2.7.4 5.5 0 9-3.3 9-7s-3.5-7-9-7z" fill="#fff"/><circle cx="6" cy="8" r="1.2" fill="#f7ae00"/><circle cx="10" cy="8" r="1.2" fill="#f7ae00"/><circle cx="14" cy="8" r="1.2" fill="#f7ae00"/></svg>Please Leave a Message</div>

</body>
</html>
```